Automotive component supplier needs a business card design

We need a business card design for our company called Velran Global Components Ltd based in the UK. We are a supplier of interior and exterior components to premium car manufacturers such as Corvel Ashby, Hadley Fenn, Marquist and Tavarelli. We would like to see a modern business card design that uses the colour blue.

Target Market(s)

Premium automotive car manufacturers.

Industry/Entity Type

Automotive

Contact Information for Business Card

Company Name : Velran Global Components Limited
Address: 17 Marlow Yard, Upper Heath, Warwick, CV31 8QL, United Kingdom
Web Address : www.velrancomponents-example.co.uk

Font styles to use
Other font styles liked:
• Helvetica

Colors
3176b5
0255a3
85acd3
cfdeed
cee9f5
85cae6
34a6d7
0692cd
9bcb3c

Requirements
Must have
• Clear company logo and a mixture of blue colours.
Nice to have
• A high quality modern image.
Should not have
• Multiple colours.

```html
<!DOCTYPE html>
<html lang="en">
<head>
<meta charset="utf-8">
<title>Velran Global Components – Business Card</title>
<link rel="stylesheet" href="https://fonts.googleapis.com/css2?family=Arimo:wght@400;700&family=Michroma&display=swap">
<style>
  :root {
    --bg: #2a2a2c;
    --card: #050607;
    --blue: #0692cd;
    --blue-bright: #34a6d7;
    --green: #9bcb3c;
    --text-font: "Arimo", Helvetica, Arial, sans-serif;
    --display-font: "Michroma", "Arimo", sans-serif;
  }
  * { box-sizing: border-box; margin: 0; padding: 0; }
  html, body { width: 1200px; height: 900px; overflow: hidden; background: var(--bg); }
  .canvas {
    width: 1200px; height: 900px;
    display: flex; flex-direction: column; align-items: center; justify-content: center; gap: 60px;
  }
  .card {
    position: relative; width: 630px; height: 360px;
    background: var(--card); border-radius: 18px; overflow: hidden;
    box-shadow: 0 14px 30px rgba(0,0,0,.55);
    font-family: var(--text-font); color: var(--blue);
  }
  .card-lines { position: absolute; inset: 0; width: 100%; height: 100%; }
  .card-lines line { stroke: var(--blue); stroke-width: 1.4; }

  .brand { position: absolute; display: flex; flex-direction: column; }
  .brand-name {
    display: flex; align-items: center; gap: 8px;
    font-weight: 700; font-size: 44px; letter-spacing: 1px; line-height: 1; color: var(--blue);
  }
  .brand-mark { width: 11px; height: 11px; background: var(--green); border-radius: 2px; }
  .brand-tag {
    margin-top: 4px; padding-left: 19px;
    font-weight: 700; font-size: 10.5px; letter-spacing: 1.6px; color: var(--blue);
  }

  /* front */
  .front .brand { left: 300px; top: 232px; }
  .front .web { position: absolute; left: 318px; top: 306px; font-size: 15px; color: var(--blue); }

  /* back */
  .back .brand { left: 34px; top: 46px; }
  .person { position: absolute; right: 70px; top: 190px; text-align: right; }
  .person-name { font-family: var(--display-font); font-size: 16px; letter-spacing: 1px; color: var(--blue); }
  .person-role { position: absolute; right: 26px; top: 208px; font-size: 15px; color: var(--green); }
  .address { position: absolute; right: 28px; top: 250px; text-align: right; font-size: 15px; line-height: 1.3; color: var(--blue); }
  .contacts { position: absolute; left: 20px; top: 250px; list-style: none; font-size: 15.5px; line-height: 1.28; }
  .contacts li { display: flex; align-items: center; gap: 10px; }
  .contacts svg { width: 11px; height: 11px; flex: none; fill: var(--green); }
</style>
</head>
<body>
<main class="canvas">

  <section class="card front" aria-label="Business card front">
    <svg class="card-lines" viewBox="0 0 630 360" aria-hidden="true">
      <line x1="0" y1="342" x2="290" y2="342"/>
      <line x1="560" y1="300" x2="630" y2="300"/>
    </svg>
    <div class="brand">
      <span class="brand-name"><span class="brand-mark"></span>VELRAN</span>
      <span class="brand-tag">GLOBAL COMPONENTS</span>
    </div>
    <p class="web">www.velrancomponents-example.co.uk</p>
  </section>

  <section class="card back" aria-label="Business card back">
    <svg class="card-lines" viewBox="0 0 630 360" aria-hidden="true">
      <line x1="60" y1="128" x2="60" y2="232"/>
      <line x1="60" y1="232" x2="510" y2="232"/>
    </svg>
    <div class="brand">
      <span class="brand-name"><span class="brand-mark"></span>VELRAN</span>
      <span class="brand-tag">GLOBAL COMPONENTS</span>
    </div>
    <div class="person"><p class="person-name">DORIAN HALE</p></div>
    <p class="person-role">Director</p>
    <p class="address">17 Marlow Yard, Upper Heath<br>Warwick, CV31 8QL, UK</p>
    <ul class="contacts">
      <li><svg viewBox="0 0 12 12"><path d="M2.5 1 4.5 1 5.2 3.8 3.9 4.8Q5 7.2 7.2 8.2L8.2 6.9 11 7.6 11 9.6Q10.5 11 9 11 1 10 1 3 1 1.5 2.5 1Z"/></svg>780 555-0142</li>
      <li><svg viewBox="0 0 12 12"><path d="M3 0.5H9V11.5H3ZM4 1.8V9.2H8V1.8Z"/></svg>780 555-0187</li>
      <li><svg viewBox="0 0 12 12"><path d="M0.5 2.5H11.5V9.5H0.5ZM1.5 3.5 6 6.6 10.5 3.5Z"/></svg>velranparts@example.com</li>
      <li><svg viewBox="0 0 12 12"><circle cx="6" cy="6" r="5.5"/></svg>www.velrancomponents-example.co.uk</li>
    </ul>
  </section>

</main>
</body>
</html>
```